BOLD & MINIMALIST DESIGN NEEDED

We want a very bold but minimalistic business card design that is impactful and utilizes both sides of the business card. Our current logo is included for your use.

We want bold fonts and good use of negative space. We don't want the logo to overpower the design.

Target Market(s)

Professionals who are building new commercial buildings.

Industry/Entity Type

Construction

Contact Information for Business Card

Name, Title, email, office phone, cell phone, website

Font styles to use
Serif
Sans Serif

Requirements
Must have
• Bold design!

```html
<!DOCTYPE html>
<html lang="en">
<head>
<meta charset="utf-8">
<title>Northvale — Business Card</title>
<link rel="stylesheet" href="https://fonts.googleapis.com/css2?family=Arimo:wght@400;700&display=swap">
<style>
  :root {
    --bg: #e8e5e0;
    --ink: #141414;
    --card-black: #121212;
    --card-white: #fbfbfb;
    --lime: #8cc63f;
    --text-light: #f2f2f2;
  }
  * { box-sizing: border-box; margin: 0; padding: 0; }
  html, body { width: 1200px; height: 1027px; overflow: hidden; }
  body {
    background: var(--bg);
    font-family: "Arimo", Arial, sans-serif;
    position: relative;
  }
  .card {
    position: absolute;
    left: 240px;
    width: 720px;
    height: 412px;
    border-radius: 4px;
    overflow: hidden;
    box-shadow: 0 10px 28px rgba(0,0,0,.22);
  }
  .card--front { top: 70px; background: var(--card-black); }
  .card--back { top: 545px; background: var(--card-white); }
  .card__shapes { position: absolute; inset: 0; width: 100%; height: 100%; }

  .brand { position: absolute; display: flex; align-items: center; gap: 14px; }
  .brand__mark { width: 22px; height: 22px; background: var(--lime); flex: none; }
  .brand__name {
    font-weight: 700;
    font-size: 44px;
    letter-spacing: 1px;
    color: var(--ink);
    line-height: 1;
  }
  .card--front .brand { left: 36px; top: 186px; }
  .card--front .brand__name { font-size: 40px; }
  .card--back .brand { left: 50%; top: 184px; transform: translateX(-50%); }

  .contact {
    position: absolute;
    left: 440px;
    top: 70px;
    color: var(--text-light);
  }
  .contact__name {
    font-weight: 700;
    font-size: 27px;
    color: var(--lime);
    letter-spacing: .5px;
  }
  .contact__title { font-size: 17px; margin-top: 2px; }
  .contact__address { font-size: 17px; line-height: 1.35; margin-top: 46px; }
  .contact__list { list-style: none; margin-top: 14px; font-size: 17px; }
  .contact__item { display: flex; align-items: center; gap: 10px; height: 26px; }
  .contact__icon { width: 20px; height: 20px; flex: none; }
</style>
</head>
<body>

<section class="card card--front" aria-label="Card front">
  <svg class="card__shapes" viewBox="0 0 720 412" aria-hidden="true">
    <path d="M0 0 L250 0 Q470 170 432 412 L0 412 Z" fill="var(--lime)"/>
    <path d="M0 0 L232 0 Q440 178 414 412 L0 412 Z" fill="var(--card-white)"/>
  </svg>

  <div class="brand">
    <span class="brand__mark"></span>
    <span class="brand__name">NORTHVALE</span>
  </div>

  <div class="contact">
    <p class="contact__name">OWEN HARLOW</p>
    <p class="contact__title">Manager</p>
    <p class="contact__address">PO Box 410, Keel Avenue<br>12 Ridge Street Ashford</p>
    <ul class="contact__list">
      <li class="contact__item">
        <svg class="contact__icon" viewBox="0 0 20 20" aria-hidden="true">
          <circle cx="10" cy="10" r="10" fill="var(--lime)"/>
          <path d="M7 5.5 L8.6 5.5 L9.3 8 L8.2 8.9 Q9.2 11 11.1 11.8 L12 10.7 L14.5 11.4 L14.5 13 Q13.8 14.5 12 14.2 Q7 13 5.8 8 Q5.5 6.2 7 5.5 Z" fill="var(--card-black)"/>
        </svg>
        <span>555.210.4478</span>
      </li>
      <li class="contact__item">
        <svg class="contact__icon" viewBox="0 0 20 20" aria-hidden="true">
          <circle cx="10" cy="10" r="10" fill="var(--lime)"/>
          <rect x="5" y="6.5" width="10" height="7" fill="var(--card-black)"/>
          <path d="M5 6.5 L10 10.5 L15 6.5" stroke="var(--lime)" stroke-width="1" fill="none"/>
        </svg>
        <span>info@northvalebuild.com</span>
      </li>
      <li class="contact__item">
        <svg class="contact__icon" viewBox="0 0 20 20" aria-hidden="true">
          <circle cx="10" cy="10" r="10" fill="var(--lime)"/>
          <g stroke="var(--card-black)" stroke-width="1.2" fill="none">
            <circle cx="10" cy="10" r="5"/>
            <ellipse cx="10" cy="10" rx="2.2" ry="5"/>
            <path d="M5 10 H15"/>
          </g>
        </svg>
        <span>www.northvalebuild.com</span>
      </li>
    </ul>
  </div>
</section>

<section class="card card--back" aria-label="Card back">
  <div class="brand">
    <span class="brand__mark"></span>
    <span class="brand__name">NORTHVALE</span>
  </div>
</section>

</body>
</html>
```